tinyTally Resource Book - 10 maths tasks to do outside

I need a 22 (11 pages back to back) page A6 sized book produced to standard for submission to professional printer. Needs to be as .pdf file showing guide lines and allowances for colour bleed. I have text already written and submitted as attachment in a Word file with margins set to A6 size. The theme of the materials is "Nature Play" so using lots of pictures from nature (Australia preferably) and showing lots of patterns in nature (rocks, leaves, flower petals etc). Some of the tasks refer to specific activities, such as "shadows" and "floating" so would be great to illustrate appropriately. The big emphasis is on learning outside the classroom, getting kids to engage actively with nature. I would like to see the pages as full colour - so not white background. The book itself will be spiral bound along the top edge so a margin of at least 1cm will be required at the top of each page (or the bottom of even numbered pages). Book will be printed on plastic laminated matte paper for outdoor use. Font size needs to be big enough to read. Fonts sizes, alignments and page numbers are all different at the moment and need to be standardised. One photo is included in a page as a sample if you can use it, otherwise disregard. Logo for Wattlebrook Numeracy Guild is also included to have as part of the acknowledgements at the back of the book.

Target Market(s)

Book is for early childhood and preschool teachers.

Industry/Entity Type

Education

Font styles to use
Sans Serif

Requirements
Must have
• Colour and appeal.
Nice to have
• Use of natural colours instead of bright catchy colours but that is your call.
Should not have
• American spelling

```html
<!DOCTYPE html>
<html lang="en-AU">
<head>
<meta charset="utf-8">
<title>Does It Float? – tinyTally</title>
<link rel="stylesheet" href="https://fonts.googleapis.com/css2?family=Jost:ital,wght@0,400;0,700;0,800;1,700&display=swap">
<style>
  :root {
    --paper: #ffffff;
    --ink-navy: #2c3990;
    --ink-body: #2b2b2b;
    --bullet-red: #d8262c;
    --crop: #555555;
    --sky: #eaf5f8;
    --leaf: #a9d25a;
    --leaf-deep: #6fa83a;
    --water-light: #bfe0f2;
    --water: #5fa6d8;
    --water-deep: #3f87c4;
  }
  * { margin: 0; padding: 0; box-sizing: border-box; }
  html, body { width: 892px; height: 1200px; overflow: hidden; background: var(--paper); }
  .sheet { position: relative; width: 892px; height: 1200px; font-family: "Jost", "Futura", sans-serif; }
  .crop-marks { position: absolute; inset: 0; }
  .page {
    position: absolute; left: 52px; top: 56px; width: 788px; height: 1088px; overflow: hidden;
  }
  .nature-backdrop {
    position: absolute; inset: 0;
    background:
      radial-gradient(ellipse 260px 360px at 60px 220px, rgba(111,168,58,.75), rgba(169,210,90,0) 70%),
      radial-gradient(ellipse 300px 160px at 330px 10px, rgba(169,210,90,.85), rgba(169,210,90,0) 70%),
      radial-gradient(ellipse 200px 380px at 770px 260px, rgba(169,210,90,.7), rgba(169,210,90,0) 70%),
      radial-gradient(ellipse 420px 200px at 420px 760px, rgba(255,255,255,.35), rgba(255,255,255,0) 70%),
      linear-gradient(180deg, var(--sky) 0%, var(--sky) 38%, var(--water-light) 55%, var(--water) 82%, var(--water-deep) 100%);
  }
  .line { position: absolute; white-space: nowrap; }
  .task-title {
    left: 0; width: 100%; top: 84px; text-align: center;
    font-weight: 800; font-size: 43px; color: var(--ink-navy);
    text-shadow: 0 0 4px #fff, 0 0 2px #fff;
  }
  .outcome-heading {
    left: 0; width: 100%; top: 124px; text-align: center;
    font-weight: 700; font-size: 30px; line-height: 42px; color: var(--ink-navy);
    text-shadow: 0 0 3px #fff;
  }
  .lead {
    font-weight: 700; font-style: italic; font-size: 23px; color: var(--ink-navy);
    line-height: 37px; left: 72px;
  }
  .body-text { font-size: 32px; line-height: 45.5px; color: var(--ink-body); left: 144px; }
  .opportunities { left: 144px; top: 795px; list-style: none; font-size: 28px; line-height: 42.5px; color: var(--ink-body); }
  .opportunities li { position: relative; padding-left: 22px; }
  .opportunities li.cont { padding-left: 22px; }
  .opportunities .diamond {
    position: absolute; left: 0; top: 15px; width: 14px; height: 14px;
    background: var(--bullet-red); transform: rotate(45deg);
  }
  .page-number { position: absolute; left: 642px; top: 934px; width: 72px; height: 72px; }
</style>
</head>
<body>
<div class="sheet">
  <svg class="crop-marks" width="892" height="1200" aria-hidden="true">
    <g stroke="var(--crop)" stroke-width="1">
      <line x1="52" y1="0" x2="52" y2="36"/><line x1="74" y1="36" x2="74" y2="74"/>
      <line x1="0" y1="56" x2="36" y2="56"/><line x1="36" y1="74" x2="74" y2="74"/>
      <line x1="840" y1="0" x2="840" y2="36"/><line x1="818" y1="36" x2="818" y2="74"/>
      <line x1="856" y1="56" x2="892" y2="56"/><line x1="818" y1="74" x2="856" y2="74"/>
      <line x1="52" y1="1164" x2="52" y2="1200"/><line x1="74" y1="1126" x2="74" y2="1164"/>
      <line x1="0" y1="1144" x2="36" y2="1144"/><line x1="36" y1="1126" x2="74" y2="1126"/>
      <line x1="840" y1="1164" x2="840" y2="1200"/><line x1="818" y1="1126" x2="818" y2="1164"/>
      <line x1="856" y1="1144" x2="892" y2="1144"/><line x1="818" y1="1126" x2="856" y2="1126"/>
    </g>
  </svg>

  <section class="page">
    <div class="nature-backdrop" role="img" aria-label="Photograph of green bamboo leaves above rippling blue water with droplets"></div>

    <h1 class="line task-title">8. Does It Float?</h1>
    <h2 class="line outcome-heading">EYLF – Outcome 4: Children are<br>confident and involved learners</h2>

    <p class="line lead" style="top:212px">Children develop a range of skills and processes<br>such as problem solving, inquiry, experimenta-<br>tion, hypothesising, researching and investigat-<br>ing when they...</p>

    <p class="line body-text" style="top:362px">manipulate objects and experiment<br>with cause and effect, trial and error,<br>and motion</p>

    <p class="line lead" style="top:496px">Educators promote this learning when they...</p>

    <p class="line body-text" style="top:533px">plan learning environments with<br>appropriate levels of challenge<br>where children are encouraged<br>to explore, experiment and take<br>appropriate risks in their learning</p>

    <p class="line lead" style="top:758px">This task provides an opportunity to:</p>

    <ul class="line opportunities">
      <li><span class="diamond"></span>explore the concepts</li>
      <li class="cont">of “cause” and “effect”</li>
      <li><span class="diamond"></span>predict and test hypotheses</li>
      <li><span class="diamond"></span>develop awareness</li>
      <li class="cont">of natural phenomena</li>
    </ul>

    <svg class="page-number" viewBox="0 0 72 72" aria-label="Page 16">
      <polygon points="36,2 70,27 57,68 15,68 2,27" fill="var(--ink-navy)"/>
      <text x="36" y="50" text-anchor="middle" font-family="Jost, sans-serif" font-size="30" fill="#fff">16</text>
    </svg>
  </section>
</div>
</body>
</html>
```